Schriftdesign für Shop-Header Bild (Schmuckhandel) / Online-Marketing Material
Wir verkaufen Schmuck im Onlineshop mit Herz
Wir benötigen den vorgegebenen Text in schöner Form, Farbe und Größe harmonisch eingefügt, in unserem Bild.
Folgender Text soll sich schick ins Bild einfügen oder in 3-D vielleicht in Schriftfarbe gold hervorheben:
Mit ganzem Herzen für Sie da!
Ihr Online -Juwelier mit Herz
Siehe auch unser altes Bild mit Text, im Shop, wie es nicht aussehen sollte: www.sonnenflocke.de

```html
<!DOCTYPE html>
<html lang="de">
<head>
<meta charset="utf-8">
<title>Shop-Header Schriftdesign – Perlenbogen</title>
<link rel="stylesheet" href="https://fonts.googleapis.com/css2?family=Great+Vibes&family=Comfortaa:wght@500&family=Cabin:wght@400&display=swap">
<style>
  :root {
    --page: #ffffff;
    --stage: #ddd5c8;
    --gold: #c39a56;
    --gold-dark: #a77c3c;
    --nav: #6b6769;
    --nav-text: #ffffff;
    --ink: #2e2e2e;
    --muted: #555555;
    --accent: #e02020;
    --cart-text: #e58a7a;
    --field: #f0f0f0;
    --satin-light: #f6f2ea;
    --satin-mid: #e9e0d2;
  }
  * { box-sizing: border-box; margin: 0; padding: 0; }
  html, body { width: 1200px; height: 960px; overflow: hidden; }
  body { position: relative; background: var(--page); font-family: "Cabin", sans-serif; }

  .stage { position: absolute; left: 0; top: 403px; width: 1200px; height: 557px; background: var(--stage); }

  .hero {
    position: absolute; overflow: hidden;
    background:
      radial-gradient(ellipse 14% 30% at 49% 52%, #f1dfb8 0%, #e4c995 45%, rgba(228,201,149,0) 100%),
      radial-gradient(ellipse 30% 45% at 95% 15%, rgba(217,191,147,.75), rgba(217,191,147,0) 70%),
      radial-gradient(ellipse 25% 40% at 10% 5%, rgba(217,191,147,.45), rgba(217,191,147,0) 70%),
      linear-gradient(160deg, var(--satin-mid) 0%, var(--satin-light) 35%, #e6ddcf 60%, var(--satin-light) 80%, var(--satin-mid) 100%);
  }
  .hero-photo { position: absolute; inset: 0; }
  .hero-claim, .hero-sub {
    position: absolute; font-family: "Great Vibes", cursive; color: var(--gold);
    white-space: nowrap; line-height: 1;
    text-shadow: 0 1px 0 rgba(255,255,255,.6), 0 2px 3px rgba(120,85,30,.25);
  }
  .hero-claim { letter-spacing: 1.4px; }
  .hero-sub { color: var(--gold-dark); }

  .hero--standalone { left: 31px; top: 47px; width: 1139px; height: 292px; }
  .hero--standalone .hero-claim { left: 6px; top: 112px; font-size: 96px; }
  .hero--standalone .hero-sub { right: 20px; top: 235px; font-size: 44px; }

  .shop { position: absolute; left: 104px; top: 451px; width: 995px; height: 454px; background: var(--page); }
  .shop-header { position: absolute; left: 0; top: 0; width: 100%; height: 117px; }
  .brand { position: absolute; left: 90px; top: 40px; width: 150px; text-align: center; font-family: "Cabin", sans-serif; font-size: 22px; color: var(--accent); }
  .meta-links { position: absolute; left: 566px; top: 14px; display: flex; gap: 15px; font-size: 9.5px; color: var(--muted); }
  .meta-links .is-active { color: var(--accent); }
  .search-label { position: absolute; left: 306px; top: 34px; font-size: 13px; color: var(--ink); }
  .search-label svg { vertical-align: middle; margin-left: 4px; }
  .search-field { position: absolute; left: 306px; top: 57px; width: 339px; height: 31px; background: var(--field); font-size: 11px; color: var(--muted); padding: 9px 20px; }
  .search-field svg { position: absolute; right: 8px; top: 5px; }
  .cart { position: absolute; left: 690px; top: 57px; width: 199px; height: 31px; background: var(--field); font-size: 11px; color: var(--cart-text); padding: 9px 20px; }
  .cart svg { position: absolute; right: 18px; top: 7px; }

  .main-nav { position: absolute; left: 0; top: 117px; width: 100%; height: 30px; background: var(--nav); }
  .main-nav span { position: absolute; top: 9px; font-family: "Comfortaa", sans-serif; font-size: 12px; color: var(--nav-text); }

  .hero--shop { left: 0; top: 147px; width: 995px; height: 257px; }
  .hero--shop .hero-claim { left: 2px; top: 100px; font-size: 84px; }
  .hero--shop .hero-sub { right: 18px; top: 209px; font-size: 38px; }
</style>
</head>
<body>
  <section class="hero hero--standalone">
    <div class="hero-photo" role="img" aria-label="Goldenes Herzanhänger-Collier auf cremefarbenem Seidenstoff"></div>
    <p class="hero-claim">Mit ganzem Herzen für Sie da!</p>
    <p class="hero-sub">Ihr Online -Juwelier mit Herz</p>
  </section>

  <div class="stage"></div>

  <main class="shop">
    <header class="shop-header">
      <div class="brand">Perlenbogen</div>
      <nav class="meta-links">
        <span class="is-active">Startseite</span><span>Anmelden</span><span>Mein Konto</span><span>Newsletter abonnieren</span><span>Kontakt</span>
      </nav>
      <div class="search-label">Nach welchem Artikel suchen Sie?<svg width="10" height="6" viewBox="0 0 10 6"><path d="M0 0h10L5 6z" fill="#e02020"/></svg></div>
      <div class="search-field">Suchen nach
        <svg width="24" height="22" viewBox="0 0 24 22"><path d="M12 21 2 11A5.5 5.5 0 0 1 12 4a5.5 5.5 0 0 1 10 7z" fill="#e02020"/><circle cx="11" cy="10" r="3" fill="none" stroke="#fff" stroke-width="1.6"/><path d="M13 12l3 3" stroke="#fff" stroke-width="1.6"/></svg>
      </div>
      <div class="cart">Ihr Warenkorb ist leer.
        <svg width="16" height="18" viewBox="0 0 16 18"><path d="M5 5V4a3 3 0 0 1 6 0v1" fill="none" stroke="#e02020" stroke-width="1.4"/><rect x="0" y="5" width="16" height="13" rx="1" fill="#e02020"/><path d="M8 15 5 12a1.6 1.6 0 0 1 3-2 1.6 1.6 0 0 1 3 2z" fill="#fff"/></svg>
      </div>
    </header>
    <nav class="main-nav">
      <span style="left:203px">KREUZ-ANHÄNGER</span>
      <span style="left:355px">ANHÄNGER/VERSCH.</span>
      <span style="left:519px">FOTO-MEDAILLONS</span>
      <span style="left:672px">OHRSCHMUCK</span>
      <span style="left:795px">ACCESSOIRES</span>
    </nav>
    <section class="hero hero--shop">
      <div class="hero-photo" role="img" aria-label="Goldenes Herzanhänger-Collier auf cremefarbenem Seidenstoff"></div>
      <p class="hero-claim">Mit ganzem Herzen für Sie da!</p>
      <p class="hero-sub">Ihr Online -Juwelier mit Herz</p>
    </section>
  </main>
</body>
</html>
```